Fern Lattice Table & Chair Rentals

We need a business card for a table and chair rental company. We rent tables and chairs for weddings, funerals, business events and parties. We want something that looks clean and elegant while not being too busy. We would like colors in the green and blue hues and avoiding anything orange. We want to make sure the font is large enough to be seen easily.

Target Market(s)

Wedding & Event Rentals

Industry/Entity Type

Events

Contact Information for Business Card

Fern Lattice, sales@fernlatticerentals.com, fernlatticerentals.com, 360-555-0182

Requirements
Must have
• Easy to read font
Should not have
• Orange anywhere in the design

```html
<!DOCTYPE html>
<html lang="en">
<head>
<meta charset="utf-8">
<title>Fern Lattice Table &amp; Chair Rentals – Business Card</title>
<link rel="stylesheet" href="https://fonts.googleapis.com/css2?family=Roboto:wght@400;700&display=swap">
<style>
  :root {
    --backdrop: #e6e9e8;
    --ink: #14201f;
    --navy: #1f3f6e;
    --ocean: #2e6f9e;
    --teal: #3a9a96;
    --sea: #8fcfb8;
    --mint: #e2f3e4;
    --line: #1c2a2a;
  }
  html, body {
    margin: 0;
    width: 1200px;
    height: 902px;
    overflow: hidden;
    background: var(--backdrop);
    font-family: "Roboto", Arial, sans-serif;
    color: var(--ink);
  }
  .canvas {
    position: relative;
    width: 1200px;
    height: 902px;
  }
  .card {
    position: absolute;
    width: 560px;
    height: 320px;
    border-radius: 4px;
    overflow: hidden;
    box-shadow: 0 10px 28px rgba(0,0,0,.18);
  }
  .card--front { left: 90px; top: 110px; }
  .card--back  { left: 550px; top: 480px; }
  .card__pattern {
    position: absolute;
    inset: 0;
    background:
      radial-gradient(ellipse at 70% 10%, var(--mint) 0%, rgba(226,243,228,0) 55%),
      radial-gradient(ellipse at 95% 70%, var(--ocean) 0%, rgba(46,111,158,0) 40%),
      linear-gradient(115deg, var(--navy) 0%, var(--ocean) 18%, var(--teal) 38%, var(--sea) 65%, var(--mint) 100%);
  }
  .brand {
    position: absolute;
    margin: 0;
    font-weight: 700;
    font-size: 54px;
    line-height: 1;
    color: var(--ink);
    letter-spacing: -0.5px;
  }
  .tagline {
    position: absolute;
    margin: 0;
    font-weight: 400;
    font-size: 27px;
    line-height: 1.2;
    color: var(--ink);
  }
  .card--front .brand   { left: 110px; top: 108px; }
  .card--front .tagline { left: 150px; top: 172px; }

  .card--back .brand   { left: 50px; top: 40px; }
  .card--back .tagline { left: 86px; top: 100px; }
  .divider {
    position: absolute;
    left: 392px;
    top: 122px;
    width: 168px;
    height: 2px;
    background: var(--line);
  }
  .company {
    position: absolute;
    left: 50px;
    top: 158px;
    margin: 0;
    font-weight: 700;
    font-size: 24px;
  }
  .contacts {
    position: absolute;
    left: 50px;
    top: 208px;
    margin: 0;
    padding: 0;
    list-style: none;
    font-size: 19px;
  }
  .contacts li {
    display: flex;
    align-items: center;
    gap: 12px;
    height: 30px;
  }
  .contacts svg { width: 16px; height: 16px; fill: none; stroke: var(--ink); stroke-width: 1.6; }
</style>
</head>
<body>
<main class="canvas">
  <section class="card card--front" aria-label="Business card front">
    <div class="card__pattern" role="img" aria-label="Low-poly faceted gradient background in navy, teal, sea green and pale mint"></div>
    <h1 class="brand">Fern Lattice</h1>
    <p class="tagline">Table and Chair Rentals</p>
  </section>

  <section class="card card--back" aria-label="Business card back">
    <div class="card__pattern" role="img" aria-label="Low-poly faceted gradient background in navy, teal, sea green and pale mint"></div>
    <h2 class="brand">Fern Lattice</h2>
    <p class="tagline">Table and Chair Rentals</p>
    <div class="divider"></div>
    <p class="company">Fernlattice Event Rentals, LLC</p>
    <ul class="contacts">
      <li>
        <svg viewBox="0 0 16 16" aria-hidden="true"><path d="M3 2h3l1.5 3.5-2 1.2a8 8 0 0 0 3.8 3.8l1.2-2L14 10v3a1 1 0 0 1-1 1A11 11 0 0 1 2 3a1 1 0 0 1 1-1z"/></svg>
        <span>360-555-0182</span>
      </li>
      <li>
        <svg viewBox="0 0 16 16" aria-hidden="true"><circle cx="8" cy="8" r="6"/><path d="M2 8h12M8 2c2 2 2 10 0 12M8 2c-2 2-2 10 0 12"/></svg>
        <span>www.fernlatticerentals.com</span>
      </li>
      <li>
        <svg viewBox="0 0 16 16" aria-hidden="true"><rect x="2" y="4" width="12" height="9"/><path d="M2 4l6 5 6-5"/></svg>
        <span>sales@fernlatticerentals.com</span>
      </li>
    </ul>
  </section>
</main>
</body>
</html>
```